Blood Testing Health App

We are looking for a graphics designer to create a web app for us so that we may insert it into a health management website system.
For branding purposes we are at www.Vantiqor.com and we are revamping our website... Example of new colors attached.
How we work...
We are a blood testing company based in the USA.
We offer a blood testing service nationwide in the USA.
We allow customers to order tests directly from us, visit a lab, have their blood drawn, or submit a urine sample, the lab tests it and they send the results back to our computer system and we share it with the customer.
The benefits of this are the customer does not need to go to the doctor and pay for the doctors visit to order these tests, which save them money. The tests are cheaper than going through the doctor. The customer simply uses us to get the test and the results and they can then take the results to their doctor... this process has saved them money. Others may be interested in regular check ups for blood work etc... and this allows them to do it with out needing a doctor, or if you have no insurance, this is a cheaper option too. We are quicker than a doctor, customers do not need appointments etc.
Hopefully you now have a better understanding as to what we do.
Here is the spec.
The app screen size is 750 px wide by 700 px high. ( A pdf is attached to show where the app is going to go, it is on page 3 of the pdf) The customer will have the ability to scroll… therefore the length of the page can be longer.
The app will consist of the following sections
Entry Page –
This will be the first page the user sees upon opening the app. This will be where they are directed from to the sections of the app discussed below. This needs to be branded for VantiQor with a modern look.
1 – Order Test (Giving them the ability to purchase a blood test within the app)
2 – VantiQor Dashboard (A dashboard that has everything they could need to use our service_
How it works Section on entry page – this will be a simple set of graphics showing how the service works. We already have the graphics for this, they do not need to be built again. They are attached to this brief
Basic structure of sections –
Order Test –
This page contains all tests, filed in categories – and Sub categories – Each test needs a link to an Information section – Price – Buy Now – Cart Process
VantiQor Dashboard –
A page of icons along the top of the app
- My Confirmation
- My Nearest Lab
- My Receipt
- My Orders
- My Account
- My Results
- My Inbox
- Contact Us
Sections in more detail -
Order A Test –
Show all categories/ sub categories – There are 23 categories, 14 sub categories, and within these categories are 300 tests - Here is the information for the categories etc - http://www.vantiqor.com/panels.aspx?PanelGroupID=4 Just in case it helps :)
We need to present this in a graphic format that is spacious, modern (brimlake, kivvo web appearance is the direction we are going for) We need it to be clear and not overwhelming to the customer.
Functionality idea…
Customer clicks category/ subcategory and tests appear.
Customer sees small 35 word description. For more information the test opens into a lightbox or expand the container which ever graphic designer believes to be most visually appealing
Buy Now must always be visible, along with price of the test
Buying process explained – Customer clicks buy now –
They are then taken to a Review Order screen ( This contains Order summary and choose payment method – insert payment details )
– Confirm payment –
Confirmation screen appears, thanking them.
They are then taken to the VantiQor Dashboard...
VantiQor Dashboard –
"My Confirmation" - Print Confirmation Order (PDF is in brief, we want this web based not a pdf download)
"My Nearest Lab Location" - This does not need to be designed because the web developer has this part under control, but we do need the icon in the dashboard
"My Receipt" - Print receipt - This does not exist in our system yet. So we need to create this from scratch - It will need to have - The test they are purchasing and the amount of the test - The customers name - The order ID - Must provide printer friendly option too
"My Orders" - This will have a list of orders - At the end of each order will be a status update of either "Test results" "Open order"
A graphic table format would be perfect. This will be linked to relevant results if they have been received. I have also attached a version of what the customer currently sees on our website. We know it is nasty ;) We are redesigning... but the information is there for this section to help design it with the right info. If the results are ready it will say in this list.
"Results Ready" will be a link to show those results once the customer has clicked the link, and the results will appear in the app, under the icons. There must be a printer friendly version too.
"My Results" Developer will sort this page out but we need the icon... It will be exactly like my orders but only show test results
"My Account" - This will be a place for them to update their personal information - Name, DOB, Address, Email Address
"My Inbox" - An inbox interface - Our way of contacting the customer for promotions we are running etc – We need a design of how this screen will appear. We also need the icon in the dashboard to have a notification on it if there are messages in the customers inbox. A little red 1, or circle with number of messages in the inbox.
"Customer Service" - This does not need to be designed because the web developer has this part under control, but we do need the icon in the dashboard
Icons appear along the top of app ( example - Mac icons/ iphone app icons) When the customer clicks an icon the content always appears below the icons
Here is more information for the icons and what should appear when each icon is clicked.
Screens to be designed –
Entry Page
Order A Test Page
Review Order Screen/Payment Screen - Show a lightbox that shows payment has been confirmed. Customer clicks close and are on the Confirmation Screen
VantiQor Dashboard - Screens mentioned in detail above
We can't wait to see your designs!
Please email any questions.
Hi all this is the first time we have used pixel harbor and understand the budget was too low for this project. We have now increased the budget to $2,000 and extended the deadline by another week
Hi all we are receiving some really great designs. I just added an example of the space that the web app will be going into... It is called "morvelapp.pdf"
Hi guys updated the brief. Hopefully this will help with the dashboard part of the design

```html
<!DOCTYPE html>
<html lang="en">
<head>
<meta charset="utf-8">
<title>VantiQor – Order a Test</title>
<link href="https://fonts.googleapis.com/css2?family=Roboto:wght@400;500;700&display=swap" rel="stylesheet">
<style>
  :root {
    --brand-green: #8fbf3c;
    --brand-dark: #3a3a3a;
    --text: #333333;
    --muted: #9a9a9a;
    --bar-grey: #e4e4e4;
    --tab-grey: #e9e9e9;
    --page: #ffffff;
    --field: #ffffff;
    --icon-light: #f6f6f6;
    --icon-mid: #d6d6d6;
    --glyph: #5f5f5f;
    --glyph-soft: #8a8a8a;
  }
  * { box-sizing: border-box; margin: 0; padding: 0; }
  html, body { width: 667px; height: 1200px; overflow: hidden; background: var(--page); }
  body { font-family: "Roboto", Arial, sans-serif; color: var(--text); position: relative; }

  .app-header { height: 86px; position: relative; }
  .brand { position: absolute; left: 14px; top: 26px; display: flex; align-items: center; gap: 8px;
           font-size: 30px; font-weight: 500; color: var(--brand-dark); letter-spacing: 0.5px; }
  .brand-mark { width: 12px; height: 12px; background: var(--brand-green); border-radius: 50%; }
  .nav-tabs { position: absolute; left: 308px; top: 22px; display: flex; }
  .nav-tab { width: 106px; height: 64px; display: flex; flex-direction: column; align-items: center;
             justify-content: center; gap: 6px; font-size: 10px; font-weight: 500; color: var(--muted); letter-spacing: 0.4px; }
  .nav-tab.is-active { background: var(--tab-grey); color: var(--brand-green); }
  .social { position: absolute; right: 18px; top: 42px; display: flex; gap: 8px; }
  .social-dot { width: 24px; height: 24px; border-radius: 50%; background: var(--brand-green); }

  .filter-bar { height: 52px; background: var(--bar-grey); display: flex; align-items: center; padding: 0 16px; gap: 12px; }
  .filter-label { font-size: 15px; font-weight: 700; color: var(--text); }
  .select { width: 200px; height: 30px; background: var(--field); display: flex; align-items: center;
            justify-content: space-between; padding: 0 10px; font-size: 13px; color: var(--text); }
  .search { margin-left: auto; width: 210px; height: 30px; background: var(--field); display: flex;
            align-items: center; justify-content: space-between; padding: 0 4px 0 10px; font-size: 12px; color: var(--muted); }
  .search-btn { width: 26px; height: 22px; background: var(--brand-dark); display: flex; align-items: center; justify-content: center; }

  .category-grid { display: grid; grid-template-columns: repeat(4, 1fr); padding: 28px 12px 0 12px; row-gap: 14px; }
  .category { display: flex; flex-direction: column; align-items: center; height: 146px; text-align: center; }
  .category-icon { width: 100px; height: 100px; border-radius: 50%;
                   background: radial-gradient(circle at 50% 35%, var(--icon-light) 0%, var(--icon-mid) 100%);
                   box-shadow: 0 2px 4px rgba(0,0,0,0.25), inset 0 -3px 6px rgba(0,0,0,0.08);
                   display: flex; align-items: center; justify-content: center; }
  .category-icon svg { width: 62px; height: 62px; }
  .g { fill: var(--glyph); }
  .gs { fill: var(--glyph-soft); }
  .ln { fill: none; stroke: var(--glyph); stroke-width: 4; stroke-linecap: round; stroke-linejoin: round; }
  .category-name { margin-top: 8px; font-size: 13px; line-height: 16px; color: var(--text); max-width: 150px; }
</style>
</head>
<body>
  <header class="app-header">
    <div class="brand"><span>VantiQor</span><span class="brand-mark"></span></div>
    <nav class="nav-tabs">
      <div class="nav-tab is-active">
        <svg width="26" height="22" viewBox="0 0 26 22"><rect x="2" y="4" width="22" height="14" rx="2" fill="none" stroke="#8fbf3c" stroke-width="2.5"/><path d="M7 11l4 4 8-8" fill="none" stroke="#8fbf3c" stroke-width="2.5"/></svg>
        ORDER A TEST
      </div>
      <div class="nav-tab">
        <svg width="26" height="22" viewBox="0 0 26 22"><rect x="3" y="3" width="20" height="15" rx="1" fill="none" stroke="#b5b5b5" stroke-width="2"/><rect x="7" y="7" width="12" height="7" fill="#d0d0d0"/></svg>
        DASHBOARD
      </div>
    </nav>
    <div class="social">
      <span class="social-dot"></span><span class="social-dot"></span><span class="social-dot"></span>
    </div>
  </header>

  <section class="filter-bar">
    <span class="filter-label">Select Category</span>
    <div class="select"><span>Allergies</span>
      <svg width="12" height="8" viewBox="0 0 12 8"><path d="M0 0h12L6 8z" fill="#333"/></svg></div>
    <div class="search"><span>Search for a test</span>
      <span class="search-btn"><svg width="14" height="14" viewBox="0 0 14 14"><circle cx="6" cy="6" r="4" fill="none" stroke="#fff" stroke-width="2"/><path d="M9 9l4 4" stroke="#fff" stroke-width="2"/></svg></span></div>
  </section>

  <main class="category-grid">
    <div class="category"><div class="category-icon"><svg viewBox="0 0 64 64" role="img" aria-label="Male figure pictogram"><rect x="10" y="10" width="44" height="44" rx="22" class="g"/></svg></div><div class="category-name">Men's Health</div></div>

    <div class="category"><div class="category-icon"><svg viewBox="0 0 64 64" role="img" aria-label="Female figure pictogram"><rect x="10" y="10" width="44" height="44" rx="22" class="gs"/></svg></div><div class="category-name">Women's Health</div></div>

    <div class="category"><div class="category-icon"><svg viewBox="0 0 64 64" role="img" aria-label="Pills"><ellipse cx="24" cy="30" rx="14" ry="9" class="g"/><ellipse cx="42" cy="38" rx="12" ry="8" class="gs"/></svg></div><div class="category-name">Most Common</div></div>

    <div class="category"><div class="category-icon"><svg viewBox="0 0 64 64" role="img" aria-label="Virus"><path class="ln" d="M32 8v10M32 46v10M8 32h10M46 32h10M15 15l7 7M42 42l7 7M49 15l-7 7M22 42l-7 7"/><circle cx="32" cy="32" r="13" class="g"/></svg></div><div class="category-name">Sexually Transmitted Diseases</div></div>

    <div class="category"><div class="category-icon"><svg viewBox="0 0 64 64" role="img" aria-label="Eye"><path class="ln" d="M6 32c8-12 18-17 26-17s18 5 26 17c-8 12-18 17-26 17S14 44 6 32z"/><circle cx="32" cy="32" r="9" class="g"/></svg></div><div class="category-name">Diabetes Detection &amp;<br>Management</div></div>

    <div class="category"><div class="category-icon"><svg viewBox="0 0 64 64" role="img" aria-label="Skin rash"><rect x="12" y="12" width="40" height="40" rx="10" class="gs"/><circle cx="24" cy="24" r="4" fill="#fff"/><circle cx="38" cy="28" r="3" fill="#fff"/><circle cx="28" cy="40" r="3.5" fill="#fff"/><circle cx="42" cy="42" r="2.5" fill="#fff"/></svg></div><div class="category-name">Allergies</div></div>

    <div class="category"><div class="category-icon"><svg viewBox="0 0 64 64" role="img" aria-label="Stethoscope"><path class="ln" d="M16 10v14a12 12 0 0 0 24 0V10M28 36v6a12 12 0 0 0 24 0v-6"/><circle cx="52" cy="32" r="6" class="g"/></svg></div><div class="category-name">Specialized</div></div>

    <div class="category"><div class="category-icon"><svg viewBox="0 0 64 64" role="img" aria-label="Liver"><path class="g" d="M8 26c0-8 10-12 24-12s24 2 24 10c0 10-12 24-26 26-10 2-22-12-22-24z"/></svg></div><div class="category-name">Hepatitis &amp;<br>Liver Function</div></div>

    <div class="category"><div class="category-icon"><svg viewBox="0 0 64 64" role="img" aria-label="Heart with pulse line"><path class="gs" d="M32 54 10 32C2 24 8 10 20 10c6 0 10 4 12 8 2-4 6-8 12-8 12 0 18 14 10 22z"/><path d="M6 32h14l5-9 7 18 5-9h21" fill="none" stroke="#fff" stroke-width="4" stroke-linejoin="round"/></svg></div><div class="category-name">Heart &amp; Stroke</div></div>

    <div class="category"><div class="category-icon"><svg viewBox="0 0 64 64" role="img" aria-label="Syringe"><g transform="rotate(-45 32 32)"><rect x="14" y="25" width="30" height="14" rx="2" class="g"/><path class="ln" d="M44 32h14M6 32h8M6 24v16"/></g></svg></div><div class="category-name">Drugs &amp; Alcohol</div></div>

    <div class="category"><div class="category-icon"><svg viewBox="0 0 64 64" role="img" aria-label="Capsule"><g transform="rotate(-40 32 32)"><rect x="8" y="22" width="48" height="20" rx="10" class="gs"/><path class="g" d="M32 22h14a10 10 0 0 1 0 20H32z"/></g></svg></div><div class="category-name">Nutrition &amp; Vitamins</div></div>

    <div class="category"><div class="category-icon"><svg viewBox="0 0 64 64" role="img" aria-label="Awareness ribbon"><path d="M20 56 40 24a9 9 0 1 0-16 0l20 32" fill="none" stroke="#5f5f5f" stroke-width="8" stroke-linejoin="round"/></svg></div><div class="category-name">Cancer Screening</div></div>

    <div class="category"><div class="category-icon"><svg viewBox="0 0 64 64" role="img" aria-label="Hazard bottle"><rect x="25" y="6" width="14" height="10" class="gs"/><rect x="14" y="16" width="36" height="42" rx="5" class="g"/><path d="M24 30l16 16M40 30 24 46" stroke="#fff" stroke-width="4" stroke-linecap="round"/></svg></div><div class="category-name">Metals &amp; Poisoning</div></div>

    <div class="category"><div class="category-icon"><svg viewBox="0 0 64 64" role="img" aria-label="Weighing scale"><rect x="10" y="10" width="44" height="44" rx="6" class="g"/><rect x="20" y="18" width="24" height="12" rx="2" fill="#fff"/><path d="M32 28l4-7" stroke="#5f5f5f" stroke-width="2"/></svg></div><div class="category-name">Weight Loss &amp; Fitness</div></div>

    <div class="category"><div class="category-icon"><svg viewBox="0 0 64 64" role="img" aria-label="Molecule"><path class="g" d="M22 12h16l8 14-8 14H22l-8-14z"/><path class="ln" d="M46 26h8M38 40l6 12"/><circle cx="54" cy="26" r="4" class="gs"/><circle cx="44" cy="52" r="4" class="gs"/></svg></div><div class="category-name">Hormone</div></div>

    <div class="category"><div class="category-icon"><svg viewBox="0 0 64 64" role="img" aria-label="Wheelchair"><circle cx="30" cy="10" r="5" class="g"/><path class="ln" d="M30 18v18h14l6 14"/><path class="ln" d="M22 28a14 14 0 1 0 20 16"/></svg></div><div class="category-name">Autoimmune Disorders<br>/ Arthritis</div></div>

    <div class="category"><div class="category-icon"><svg viewBox="0 0 64 64" role="img" aria-label="Thyroid pictogram"><rect x="12" y="12" width="40" height="40" rx="20" class="g"/></svg></div><div class="category-name">Thyroid / Parathyroid</div></div>

    <div class="category"><div class="category-icon"><svg viewBox="0 0 64 64" role="img" aria-label="IV drip bag"><rect x="18" y="6" width="28" height="34" rx="6" class="g"/><path class="ln" d="M32 40v10"/><path class="gs" d="M28 50h8l-4 8z"/></svg></div><div class="category-name">Infectious Disease</div></div>

    <div class="category"><div class="category-icon"><svg viewBox="0 0 64 64" role="img" aria-label="Blood drop"><path class="g" d="M32 6C26 18 16 28 16 40a16 16 0 0 0 32 0C48 28 38 18 32 6z"/></svg></div><div class="category-name">Blood disease</div></div>

    <div class="category"><div class="category-icon"><svg viewBox="0 0 64 64" role="img" aria-label="Stomach"><path d="M24 8v14c0 8 20 4 22 16 2 12-10 18-22 14-6-2-10-6-12-2" fill="none" stroke="#5f5f5f" stroke-width="11" stroke-linecap="round"/></svg></div><div class="category-name">Digestive disorders</div></div>

    <div class="category"><div class="category-icon"><svg viewBox="0 0 64 64" role="img" aria-label="Kidneys"><ellipse cx="20" cy="32" rx="11" ry="17" class="g"/><ellipse cx="44" cy="32" rx="11" ry="17" class="g"/><path class="ln" d="M28 36l4 20M36 36l-4 20" stroke="#8a8a8a"/></svg></div><div class="category-name">Kidney<br>/ Adrenal Gland</div></div>

    <div class="category"><div class="category-icon"><svg viewBox="0 0 64 64" role="img" aria-label="Pregnancy pictogram"><rect x="12" y="12" width="40" height="40" rx="20" class="gs"/></svg></div><div class="category-name">Pregnancy &amp; Fertility</div></div>
  </main>
</body>
</html>
```